MRT Property - Business Cards

Looking for a business card & general letterhead, signage etc design for our new logo.

Colours:
000a20
0056a2
00b5ef
0088ce
68cef2

Fonts:
Poppins
Karla

Please keep look and feel of new brand - example in the zip package I sent.

```html
<!DOCTYPE html>
<html lang="en">
<head>
<meta charset="utf-8">
<title>MRT Property – Stationery</title>
<link rel="stylesheet" href="https://fonts.googleapis.com/css2?family=Poppins:wght@400;500;600&display=swap">
<style>
  :root {
    --navy: #000a20;
    --ink: #0d1428;
    --blue: #0056a2;
    --mid: #0088ce;
    --cyan: #00b5ef;
    --sky: #68cef2;
    --bg: #8c8c8c;
    --paper: #ffffff;
    --text: #1b1b1b;
  }
  * { box-sizing: border-box; margin: 0; padding: 0; }
  html, body { width: 1200px; height: 686px; overflow: hidden; }
  body {
    background: var(--bg);
    font-family: "Poppins", sans-serif;
    position: relative;
  }

  /* Letterhead */
  .letterhead {
    position: absolute; left: 90px; top: 38px;
    width: 430px; height: 610px;
    background: var(--paper);
    box-shadow: 0 6px 18px rgba(0,0,0,.25);
    overflow: hidden;
  }
  .brand {
    font-weight: 600; color: var(--blue);
    display: flex; align-items: center; gap: 8px;
    white-space: nowrap;
  }
  .brand-mark { background: var(--cyan); }
  .letterhead .brand { position: absolute; right: 34px; top: 40px; font-size: 24px; }
  .letterhead .brand-mark { width: 16px; height: 16px; }
  .letterhead-contact {
    position: absolute; right: 34px; top: 100px;
    padding-left: 14px; border-left: 1.5px solid var(--blue);
    font-size: 9px; line-height: 1.55; color: var(--text);
  }
  .contact-row { display: flex; align-items: center; gap: 6px; }
  .contact-row svg { width: 9px; height: 9px; flex: none; }
  .letterhead-swoosh { position: absolute; left: 0; bottom: 0; width: 430px; height: 260px; }

  /* Business cards */
  .card {
    position: absolute; width: 380px; height: 218px;
    box-shadow: 0 6px 16px rgba(0,0,0,.3);
    overflow: hidden;
  }
  .card-front { left: 580px; top: 372px; background: var(--ink); color: #fff; }
  .card-back { left: 700px; top: 86px; background: var(--blue); display: flex; align-items: center; justify-content: center; }
  .card-back .brand { color: var(--sky); font-size: 30px; }
  .card-back .brand-mark { width: 20px; height: 20px; }

  .card-front .brand { position: absolute; right: 40px; top: 26px; font-size: 20px; color: var(--sky); }
  .card-front .brand-mark { width: 13px; height: 13px; }
  .card-contact {
    position: absolute; left: 22px; top: 34px;
    font-size: 8.5px; line-height: 1.7; color: #fff;
  }
  .card-holder { position: absolute; right: 30px; top: 100px; text-align: right; }
  .holder-name { font-size: 17px; font-weight: 500; color: var(--mid); }
  .holder-name .surname { color: var(--sky); }
  .holder-role { font-size: 8.5px; color: #fff; }
  .holder-tab { position: absolute; right: 0; top: 104px; width: 20px; height: 24px; background: var(--sky); }
  .card-address {
    position: absolute; right: 30px; bottom: 18px;
    text-align: right; font-size: 8.5px; line-height: 1.5;
  }
  .card-swoosh { position: absolute; left: 0; bottom: 0; width: 200px; height: 170px; }
</style>
</head>
<body>

<section class="letterhead" aria-label="Letterhead">
  <div class="brand"><span class="brand-mark"></span>MRT Property</div>
  <div class="letterhead-contact">
    <div class="contact-row">
      <svg viewBox="0 0 10 10"><path d="M2 1l2 2-1 1.2c.6 1.3 1.5 2.2 2.8 2.8L7 6l2 2-1.4 1.4C4.5 9 1 5.5.6 2.4z" fill="var(--blue)"/></svg>+61 2 9000 1234</div>
    <div class="contact-row">
      <svg viewBox="0 0 10 10"><circle cx="5" cy="5" r="4" fill="none" stroke="var(--blue)"/><path d="M1 5h8M5 1c-2 2.5-2 5.5 0 8M5 1c2 2.5 2 5.5 0 8" fill="none" stroke="var(--blue)" stroke-width=".7"/></svg>www.mrtproperty.com.au</div>
    <div class="contact-row">
      <svg viewBox="0 0 10 10"><rect x=".5" y="2" width="9" height="6" fill="none" stroke="var(--blue)"/><path d="M.5 2L5 5.5 9.5 2" fill="none" stroke="var(--blue)"/></svg>info@mrtproperty.com.au</div>
    <div class="contact-row">
      <svg viewBox="0 0 10 10"><path d="M5 .5a3.2 3.2 0 0 0-3.2 3.2C1.8 6 5 9.5 5 9.5S8.2 6 8.2 3.7A3.2 3.2 0 0 0 5 .5z" fill="var(--blue)"/><circle cx="5" cy="3.7" r="1.2" fill="#fff"/></svg>Suite 4.12, Block 3</div>
    <div style="padding-left:15px">18 Harbourline Road<br>Riverside NSW 2150</div>
  </div>
  <svg class="letterhead-swoosh" viewBox="0 0 430 260" preserveAspectRatio="none" aria-hidden="true">
    <path d="M0 0 C40 90 150 190 300 260 L0 260 Z" fill="var(--sky)"/>
    <path d="M0 30 C40 110 140 200 270 260 L0 260 Z" fill="#fff"/>
    <path d="M0 40 C45 120 140 205 255 260 L0 260 Z" fill="var(--blue)"/>
  </svg>
</section>

<section class="card card-back" aria-label="Business card back">
  <div class="brand"><span class="brand-mark"></span>MRT Property</div>
</section>

<section class="card card-front" aria-label="Business card front">
  <svg class="card-swoosh" viewBox="0 0 200 170" preserveAspectRatio="none" aria-hidden="true">
    <path d="M0 0 C30 70 100 135 190 170 L0 170 Z" fill="var(--sky)"/>
    <path d="M0 28 C30 90 90 145 165 170 L0 170 Z" fill="var(--ink)"/>
    <path d="M0 38 C32 100 90 150 150 170 L0 170 Z" fill="var(--blue)"/>
  </svg>
  <div class="brand"><span class="brand-mark"></span>MRT Property</div>
  <div class="card-contact">
    <div class="contact-row"><svg viewBox="0 0 10 10"><path d="M2 1l2 2-1 1.2c.6 1.3 1.5 2.2 2.8 2.8L7 6l2 2-1.4 1.4C4.5 9 1 5.5.6 2.4z" fill="var(--sky)"/></svg>+61 2 9000 1234</div>
    <div class="contact-row"><svg viewBox="0 0 10 10"><circle cx="5" cy="5" r="4" fill="none" stroke="var(--sky)"/><path d="M1 5h8M5 1c-2 2.5-2 5.5 0 8M5 1c2 2.5 2 5.5 0 8" fill="none" stroke="var(--sky)" stroke-width=".7"/></svg>www.mrtproperty.com.au</div>
    <div class="contact-row"><svg viewBox="0 0 10 10"><rect x=".5" y="2" width="9" height="6" fill="none" stroke="var(--sky)"/><path d="M.5 2L5 5.5 9.5 2" fill="none" stroke="var(--sky)"/></svg>info@mrtproperty.com.au</div>
  </div>
  <div class="card-holder">
    <div class="holder-name">Liam <span class="surname">Porter</span></div>
    <div class="holder-role">Director</div>
  </div>
  <div class="holder-tab"></div>
  <div class="card-address">Suite 4.12, Block 3<br>18 Harbourline Road<br>Riverside NSW 2150</div>
</section>

</body>
</html>
```